Why Use Me?

Need to create several flyers to promote myself and various home mortgage loan products. I am a loan officer within a larger company so I'm looking for an attractive flyer frame that incorporates my company's colors & logo BUT it has my own custom look and feel. Once this frame is created, I'll have several ideas for body filler. I'm looking for a logo or moniker for myself, synonymous with my business.

```html
<!DOCTYPE html>
<html lang="en">
<head>
<meta charset="utf-8">
<title>Why Use Me – Loan Officer Flyer</title>
<link href="https://fonts.googleapis.com/css2?family=Cinzel:wght@400;600;700&display=swap" rel="stylesheet">
<style>
  :root {
    --page-bg: #1d1d1f;
    --sky-blue: #1fa9e1;
    --navy: #16245a;
    --charcoal: #333538;
    --ring-grey: #58595b;
    --white: #ffffff;
    --photo-light: #e9ebee;
    --photo-mid: #b9c3cf;
    --photo-deep: #6f86a6;
  }
  * { margin: 0; padding: 0; box-sizing: border-box; }
  html, body { width: 972px; height: 1200px; overflow: hidden; background: var(--page-bg); }
  .canvas { position: relative; width: 972px; height: 1200px; overflow: hidden; }
  .flyer {
    position: absolute; left: 22px; top: 0;
    width: 1138px; height: 1473px;
    transform: scale(0.8147); transform-origin: top left;
    overflow: hidden; background: var(--photo-light);
    font-family: "Cinzel", serif; color: var(--white);
  }
  .hero-photo {
    position: absolute; left: 0; top: 0; width: 1138px; height: 720px;
    background: linear-gradient(110deg, var(--photo-deep) 0%, var(--photo-mid) 35%, var(--photo-light) 60%, #cfd4db 100%);
  }
  .backdrop { position: absolute; inset: 0; }
  .brand {
    position: absolute; left: 620px; top: 72px; width: 484px;
    display: flex; align-items: center; justify-content: flex-end; gap: 18px;
    color: var(--navy); font-weight: 700;
  }
  .brand-dot { width: 40px; height: 40px; border-radius: 50%; background: var(--navy); }
  .brand-name { font-size: 33px; line-height: 1.05; text-align: right; letter-spacing: 1px; }
  .portrait {
    position: absolute; left: 649px; top: 391px; width: 480px; height: 480px;
    border-radius: 50%; border: 11px solid var(--ring-grey);
    background: radial-gradient(circle at 50% 40%, #f4f4f4 0%, #dcdcdc 45%, #2a2c33 75%);
  }
  .headline { position: absolute; left: 95px; top: 612px; }
  .headline-kicker { font-size: 54px; font-weight: 400; letter-spacing: 1px; line-height: 1; }
  .headline-main { font-size: 77px; font-weight: 700; color: var(--sky-blue); line-height: 1; margin-top: 8px; white-space: nowrap; }
  .reasons { list-style: none; position: absolute; left: 92px; top: 0; }
  .reason {
    position: absolute; left: 0; width: 580px;
    display: flex; gap: 14px; font-size: 28px; line-height: 30px; white-space: nowrap;
  }
  .reason svg { flex: none; margin-top: 4px; }
  .profile {
    position: absolute; right: 61px; top: 1072px; text-align: right;
  }
  .profile-title { font-size: 31px; font-weight: 600; letter-spacing: 1px; line-height: 44px; }
  .profile-line { font-size: 19px; line-height: 22px; }
  .profile-line.nmls { font-size: 20px; margin-bottom: 9px; }
  .contacts { position: absolute; right: 61px; top: 1252px; text-align: right; }
  .contact { display: flex; justify-content: flex-end; align-items: center; gap: 10px; font-size: 24px; line-height: 30px; }
  .contact.web { font-size: 23px; }
  .contact.first-web { margin-top: 9px; }
</style>
</head>
<body>
<div class="canvas">
  <div class="flyer">
    <div class="hero-photo" role="img" aria-label="Photo of a smiling young family hugging on a couch in a bright living room"></div>

    <svg class="backdrop" width="1138" height="1473" viewBox="0 0 1138 1473" aria-hidden="true">
      <path fill="var(--sky-blue)" d="M0 612 C230 470 520 350 800 345 L830 345 L960 720 L1138 720 L1138 1473 L0 1473 Z"/>
      <path fill="var(--navy)" d="M1138 530 L1138 1473 L300 1473 Q268 1450 300 1428 C470 1330 640 1170 760 1040 C820 980 870 910 900 870 L900 530 Z"/>
      <path fill="var(--charcoal)" d="M0 627 C230 505 520 412 790 414 L760 860 C640 1000 470 1160 300 1262 C200 1330 100 1420 22 1473 L0 1473 Z"/>
    </svg>

    <div class="brand">
      <span class="brand-dot"></span>
      <span class="brand-name">SUMMIT RIDGE<br>LENDING</span>
    </div>

    <div class="portrait" role="img" aria-label="Portrait of the loan officer in a dark suit and blue tie"></div>

    <div class="headline">
      <p class="headline-kicker">CONCERNING</p>
      <p class="headline-main">WHY USE ME:</p>
    </div>

    <ul class="reasons">
      <li class="reason" style="top:766px"><svg width="26" height="26" viewBox="0 0 26 26"><circle cx="12" cy="14" r="10" fill="none" stroke="var(--sky-blue)" stroke-width="2.5"/><path d="M7 13 L11.5 18 L24 3" fill="none" stroke="var(--sky-blue)" stroke-width="3"/></svg><span>I’M 17 YEARS AT THE SAME EXACT<br>MORTGAGE COMPANY</span></li>
      <li class="reason" style="top:846px"><svg width="26" height="26" viewBox="0 0 26 26"><circle cx="12" cy="14" r="10" fill="none" stroke="var(--sky-blue)" stroke-width="2.5"/><path d="M7 13 L11.5 18 L24 3" fill="none" stroke="var(--sky-blue)" stroke-width="3"/></svg><span>VERY KNOWLEDGEABLE</span></li>
      <li class="reason" style="top:896px"><svg width="26" height="26" viewBox="0 0 26 26"><circle cx="12" cy="14" r="10" fill="none" stroke="var(--sky-blue)" stroke-width="2.5"/><path d="M7 13 L11.5 18 L24 3" fill="none" stroke="var(--sky-blue)" stroke-width="3"/></svg><span>ABOVE AND BEYOND SERVICE<br>AND AVAILABILITY</span></li>
      <li class="reason" style="top:976px"><svg width="26" height="26" viewBox="0 0 26 26"><circle cx="12" cy="14" r="10" fill="none" stroke="var(--sky-blue)" stroke-width="2.5"/><path d="M7 13 L11.5 18 L24 3" fill="none" stroke="var(--sky-blue)" stroke-width="3"/></svg><span>CONVERSION OF TOUGH LOANS</span></li>
      <li class="reason" style="top:1026px"><svg width="26" height="26" viewBox="0 0 26 26"><circle cx="12" cy="14" r="10" fill="none" stroke="var(--sky-blue)" stroke-width="2.5"/><path d="M7 13 L11.5 18 L24 3" fill="none" stroke="var(--sky-blue)" stroke-width="3"/></svg><span>“BUILD A BUYER” PROGRAM</span></li>
      <li class="reason" style="top:1076px"><svg width="26" height="26" viewBox="0 0 26 26"><circle cx="12" cy="14" r="10" fill="none" stroke="var(--sky-blue)" stroke-width="2.5"/><path d="M7 13 L11.5 18 L24 3" fill="none" stroke="var(--sky-blue)" stroke-width="3"/></svg><span>EXCELLENT FOLLOW-UP</span></li>
      <li class="reason" style="top:1118px"><svg width="26" height="26" viewBox="0 0 26 26"><circle cx="12" cy="14" r="10" fill="none" stroke="var(--sky-blue)" stroke-width="2.5"/><path d="M7 13 L11.5 18 L24 3" fill="none" stroke="var(--sky-blue)" stroke-width="3"/></svg><span>I WORK WITH A SEASONED<br>LENDING TEAM</span></li>
    </ul>

    <div class="profile">
      <p class="profile-title">SR. LOAN OFFICER</p>
      <p class="profile-line nmls">NMLS# 512708</p>
      <p class="profile-line">LICENSED STATES: NV, TX, AZ, OR</p>
      <p class="profile-line">FHA, CONVENTIONAL, VA, PRIVATE MONEY</p>
    </div>

    <div class="contacts">
      <p class="contact"><svg width="22" height="22" viewBox="0 0 22 22"><circle cx="11" cy="11" r="11" fill="var(--white)"/><path d="M7 5 L9.5 5 L10.5 8 L9 9.3 Q10.5 12.5 12.7 13 L14 11.5 L17 12.5 L17 15 Q16 17 13.5 16.5 Q7 14.5 5.5 8.5 Q5.5 5.5 7 5Z" fill="var(--navy)"/></svg><span>(555) 014-0905</span></p>
      <p class="contact"><svg width="22" height="22" viewBox="0 0 22 22"><circle cx="11" cy="11" r="11" fill="var(--white)"/><rect x="7" y="4" width="8" height="14" rx="1.5" fill="var(--navy)"/><rect x="8.5" y="6" width="5" height="8" fill="var(--white)"/></svg><span>(555) 017-9933</span></p>
      <p class="contact"><svg width="22" height="22" viewBox="0 0 22 22"><circle cx="11" cy="11" r="11" fill="var(--white)"/><rect x="6" y="9" width="10" height="6" rx="1" fill="var(--navy)"/><rect x="8" y="5" width="6" height="4" fill="var(--navy)"/><rect x="8" y="13" width="6" height="4" fill="var(--navy)"/></svg><span>(555) 012-7512</span></p>
      <p class="contact web first-web"><svg width="22" height="22" viewBox="0 0 22 22"><circle cx="11" cy="11" r="11" fill="var(--white)"/><rect x="5.5" y="7" width="11" height="8" fill="var(--navy)"/><path d="M5.5 7 L11 11.5 L16.5 7" fill="none" stroke="var(--white)" stroke-width="1.2"/></svg><span>MREYES@SUMMITRIDGE.COM</span></p>
      <p class="contact web"><svg width="22" height="22" viewBox="0 0 22 22"><circle cx="11" cy="11" r="10" fill="none" stroke="var(--white)" stroke-width="2"/><ellipse cx="11" cy="11" rx="4" ry="9" fill="none" stroke="var(--white)" stroke-width="1.5"/><path d="M2 11 H20" stroke="var(--white)" stroke-width="1.5"/></svg><span>MARCREYES.SUMMITRIDGE.COM</span></p>
    </div>
  </div>
</div>
</body>
</html>
```